Business Card for a Life Coaching Company

MOSSVALE is a Life Coaching company that was initiated to support people who want to transform thier life or ana aspect of it.
our slogan is : "Dream. Believe. Succeed"
our logo is uploaded.
The name of the company implies that leadership, strength and wisdom required to change your life.
We want an attractive business card that would give an impression of reliability, support and change. so we really want it unique. Here are some examples of unique cards:

http://www.pixelharbornotes.example/2009/05/100-really-creative-business-cards/

MossVale is a life coaching organization focusing on individual transformation through the application of relevant and timeless principles of success.  MossVale believes that real, sustainable life transformations are brought about by tuning into the timeless wisdom we each carry in our hearts while boldy acting in the direction of our dreams.

Contacts on the card:
Address: 7 Tarek Ibn Nabil Heliopolis Cairo Egypt
Tel: +202 24 81 37 52
Fax: +202 24 81 37 19
Mobile: +2 012 574 9026 (Nadia Sherif)
+2 0199915815 (Kamal Rashidi)

By the way, our temporary website is http://www.mossvale.example

We have attached an .eps file with various configurations of our logo.

```html
<!DOCTYPE html>
<html lang="en">
<head>
<meta charset="utf-8">
<title>MossVale Business Cards</title>
<link rel="stylesheet" href="https://fonts.googleapis.com/css2?family=Tinos&display=swap">
<style>
  :root {
    --page-bg: #ececec;
    --card-bg: #111111;
    --teal: #6fd3d6;
    --teal-light: #c9f1f1;
    --white: #ffffff;
    --contact: #f2f2f2;
    --muted: #bfc6c6;
  }
  html, body {
    margin: 0;
    width: 1200px;
    height: 840px;
    overflow: hidden;
    background: var(--page-bg);
  }
  .canvas {
    position: relative;
    width: 1200px;
    height: 840px;
  }
  .card {
    position: absolute;
    background: var(--card-bg);
    overflow: hidden;
  }
  .card--front { left: 92px; top: 104px; width: 270px; height: 449px; }
  .card--back { left: 382px; top: 104px; width: 270px; height: 449px; }
  .card--landscape { left: 671px; top: 284px; width: 449px; height: 269px; }

  .emblem {
    position: absolute;
    border-radius: 50%;
    background: radial-gradient(circle at 40% 45%, var(--white) 0%, var(--teal-light) 35%, var(--teal) 75%, rgba(111,211,214,0) 100%);
    opacity: 0.85;
  }
  .card--front .emblem { left: 20px; top: 78px; width: 230px; height: 240px; }
  .card--back .emblem { left: 160px; top: 40px; width: 220px; height: 230px; }
  .card--landscape .emblem { left: 14px; top: 30px; width: 190px; height: 200px; }

  .slogan {
    position: absolute;
    margin: 0;
    font-family: "Tinos", serif;
    font-size: 14px;
    letter-spacing: 0.4px;
    color: var(--muted);
    white-space: nowrap;
  }
  .card--front .slogan { left: 0; right: 0; top: 40px; text-align: center; }
  .card--landscape .slogan { left: 212px; top: 150px; }

  .brand-name {
    position: absolute;
    margin: 0;
    font-family: "Tinos", serif;
    font-weight: 400;
    font-size: 36px;
    line-height: 1;
    letter-spacing: 1px;
    color: var(--teal);
    white-space: nowrap;
  }
  .card--front .brand-name { left: 0; right: 0; top: 380px; text-align: center; }
  .card--landscape .brand-name { left: 210px; top: 100px; }

  .website {
    position: absolute;
    left: 15px;
    top: 271px;
    margin: 0;
    font-family: "Tinos", serif;
    font-size: 13px;
    letter-spacing: 0.3px;
    color: var(--white);
  }
  .contact {
    position: absolute;
    left: 12px;
    top: 326px;
    margin: 0;
    font-family: "Tinos", serif;
    font-size: 12.5px;
    line-height: 18px;
    color: var(--contact);
    font-style: normal;
  }
</style>
</head>
<body>
<main class="canvas">
  <section class="card card--front">
    <p class="slogan">Dream. Believe. Succeed.</p>
    <div class="emblem" role="img" aria-label="MossVale brand emblem area"></div>
    <h1 class="brand-name">MOSS VALE</h1>
  </section>

  <section class="card card--back">
    <div class="emblem" role="img" aria-label="MossVale brand emblem area, cropped at the edge"></div>
    <p class="website">WWW.MOSSVALE.EXAMPLE</p>
    <address class="contact">
      Tel: +202 24 81 37 52<br>
      Fax: +202 24 81 37 19<br>
      Mobile: (Nadia Sherif) +2 012 574 9026<br>
      Address: 7 Tarek Ibn Nabil<br>
      Heliopolis Cairo Egypt
    </address>
  </section>

  <section class="card card--landscape">
    <div class="emblem" role="img" aria-label="MossVale brand emblem area"></div>
    <h2 class="brand-name">MOSS VALE</h2>
    <p class="slogan">Dream. Believe. Succeed.</p>
  </section>
</main>
</body>
</html>
```